Micro Markets Vending business needs a web design

I purchased a logo through MarkHarbor and asked them to design my website but was told they couldn't and that I needed to contact you.
I was building a website through Plume using AI and liked what they had created verbiage-wise but I can't figure out how to finish it the way I would like it. Will send screen shots of what was written, and subsequently used in my slogan under my logo. Would like to use the colors in my logo for my website.
About the company:
RT Snackworks, LLC offers micro market vending machines. Swipe your card, open the doors, take what you want. Can be customized by size for the space, and items for sale within the machines. Pictures of the machines are attached as examples.
I don't need a Testimonials page right now since we are a new company, but will need to add one at some point.
I also like the idea of a contact us button, as shown in the last picture (although it says subscribe). We do not have any emails set up as of yet. Haven't figured out how to do that, but will.
Just let me know what files you need from MarkHarbor for my logo.
Target Market(s)
Apartment complexes, Buildings, Hotels, Gyms, etc
Industry/Entity Type
Vending Machines
Coding
Coded - Design and coding required
Number of Pages Required
1 page
Font styles to use
Other font styles liked:
- Your choice on font style that complements our logo font.
Look and feel
Each slider illustrates characteristics of the customer's brand and the style your logo design should communicate.

```html
<!DOCTYPE html>
<html lang="en">
<head>
<meta charset="utf-8">
<title>RT Snackworks, LLC</title>
<link href="https://fonts.googleapis.com/css2?family=Barlow:wght@500;600;700&family=Source+Sans+3:ital,wght@0,400;0,600;1,400&display=swap" rel="stylesheet">
<style>
:root{
  --green:#2e8b3a;
  --green-dark:#1f6e2b;
  --lime:#8cc63f;
  --ink:#111;
  --text:#555;
  --muted-bg:#f1f1f1;
  --navy:#0d1d3a;
  --footer:#141414;
  --white:#fff;
}
*{box-sizing:border-box;margin:0;padding:0}
html,body{width:1200px;height:3402px;overflow:hidden}
body{font-family:"Source Sans 3",sans-serif;color:var(--text);background:var(--white);position:relative}
section,footer,header{position:absolute;left:0;width:1200px}
.abs{position:absolute}
.btn{position:absolute;display:flex;align-items:center;justify-content:center;background:linear-gradient(180deg,var(--lime),var(--green));color:var(--white);font-family:"Barlow",sans-serif;font-weight:600;font-size:15px;border-radius:6px;letter-spacing:.3px}
.brand{display:flex;align-items:center;gap:10px;font-family:"Barlow",sans-serif;font-weight:600;color:var(--white);font-size:21px}
.brand-mark{width:20px;height:20px;background:var(--green)}
.section-title{position:absolute;left:0;width:100%;text-align:center;font-family:"Barlow",sans-serif;font-weight:700;font-size:35px;color:var(--ink)}
.section-title span{color:var(--green);font-weight:500}
.rule{position:absolute;height:4px;width:66px;background:var(--green)}
/* hero */
.hero{top:0;height:573px;background:var(--navy)}
.hero-photo{position:absolute;inset:0;background:linear-gradient(90deg,#0b1a38 0%,#13284a 40%,#3a5f6a 62%,#c27a3a 72%,#4f7c86 85%,#9fb4bc 100%)}
.hero-shade{position:absolute;inset:0;background:linear-gradient(90deg,rgba(10,22,48,.95) 0%,rgba(10,22,48,.7) 45%,rgba(10,22,48,0) 65%)}
.nav a{position:absolute;top:54px;font-family:"Barlow",sans-serif;font-weight:600;font-size:15px;color:var(--white);text-decoration:none}
.nav a.active{color:var(--lime)}
.hero h2{position:absolute;left:111px;top:193px;font-family:"Source Sans 3",sans-serif;font-weight:400;font-size:25px;color:var(--white)}
.hero h1{position:absolute;left:111px;top:234px;font-family:"Barlow",sans-serif;font-weight:700;font-size:40px;letter-spacing:3px;color:var(--white)}
.hero .tagline{position:absolute;left:111px;top:291px;font-family:"Barlow",sans-serif;font-weight:600;font-size:13px;letter-spacing:3px;color:var(--lime)}
.hero p{position:absolute;left:111px;top:320px;width:400px;font-size:17px;line-height:24px;color:var(--white)}
/* about */
.about{top:573px;height:523px}
.about-photo{position:absolute;left:111px;top:87px;width:457px;height:347px;border-radius:14px;background:linear-gradient(135deg,#5a3a2a,#1b2b3a 40%,#3b6ea0 60%,#2a2a2a)}
.about h3{position:absolute;left:643px;top:80px;font-family:"Barlow",sans-serif;font-weight:700;font-size:34px;color:var(--ink)}
.about h3 span{color:var(--green);font-weight:500}
.about p{position:absolute;left:643px;width:465px;font-size:16px;line-height:24px}
/* why */
.why{top:1096px;height:629px;background:var(--muted-bg)}
.why .lead{position:absolute;left:250px;width:700px;top:128px;text-align:center;font-style:italic;font-size:17px;line-height:24px}
.card{position:absolute;background:var(--white);border-radius:10px;box-shadow:0 2px 8px rgba(0,0,0,.06);text-align:center}
.icon{position:absolute;width:86px;height:86px;border-radius:50%;background:var(--green);left:50%;margin-left:-43px;top:-21px;display:flex;align-items:center;justify-content:center}
.card h4{position:absolute;left:0;width:100%;top:81px;font-family:"Barlow",sans-serif;font-weight:600;font-size:17px;color:var(--ink);letter-spacing:.3px}
.card p{position:absolute;left:16px;right:16px;top:118px;font-size:16.5px;line-height:24px}
.card .more{position:absolute;left:0;width:100%;bottom:42px;font-family:"Barlow",sans-serif;font-weight:600;font-size:15px;color:var(--green);text-decoration:underline}
/* portfolio */
.portfolio{top:1725px;height:752px}
.tile{position:absolute;border-radius:6px}
/* blog */
.blog{top:2477px;height:656px}
.post{position:absolute;top:141px;width:309px;height:435px;background:var(--white);border-radius:12px;box-shadow:0 2px 10px rgba(0,0,0,.1);text-align:center}
.post-photo{position:absolute;left:0;top:0;width:309px;height:229px;border-radius:12px;background:linear-gradient(135deg,#2b2b2b,#6e5a4a 45%,#b54a3a 75%,#d7d7d7)}
.post h4{position:absolute;left:0;width:100%;top:256px;font-family:"Barlow",sans-serif;font-weight:600;font-size:21px;color:var(--ink)}
.post p{position:absolute;left:10px;right:10px;top:293px;font-size:16px;line-height:23px}
.post .more{position:absolute;left:0;width:100%;top:392px;font-family:"Barlow",sans-serif;font-weight:600;font-size:15px;color:var(--green);text-decoration:underline}
.arrow{position:absolute;top:2809px;width:34px;height:34px;border-radius:50%}
/* footer */
.site-footer{top:3133px;height:269px;background:var(--footer);color:var(--white)}
.site-footer .links a{position:absolute;top:173px;font-family:"Barlow",sans-serif;font-weight:600;font-size:15px;color:var(--white);text-decoration:none}
.site-footer hr{position:absolute;left:111px;width:978px;top:217px;border:0;border-top:1px solid #3a3a3a}
.copy{position:absolute;left:0;width:100%;top:238px;text-align:center;font-size:13px}
.copy a{color:var(--white)}
</style>
</head>
<body>

<header class="hero">
  <div class="hero-photo" role="img" aria-label="Close-up of a lit vending machine stocked with snacks and drinks in a bright lobby"></div>
  <div class="hero-shade"></div>
  <div class="abs" style="left:111px;top:76px">
    <div class="brand"><span class="brand-mark"></span>RT Snackworks, LLC</div>
  </div>
  <nav class="nav">
    <a class="active" style="left:463px">HOME</a>
    <a style="left:580px">ABOUT US</a>
    <a style="left:728px">WHY CHOOSE US</a>
  </nav>
  <a class="btn" style="left:965px;top:40px;width:124px;height:46px">CONTACT US</a>
  <h2>WELCOME TO</h2>
  <h1>RT SNACKWORKS, LLC</h1>
  <div class="tagline">WHERE CONVENIENCE MEETS CUSTOMIZATION</div>
  <p>Welcome to RT Snackworks, where convenience meets customization. Our micro market vending...</p>
  <a class="btn" style="left:111px;top:385px;width:123px;height:46px">GET STARTED</a>
</header>

<section class="about">
  <div class="about-photo" role="img" aria-label="Two-door micro market cooler filled with snacks and drinks against a brick wall"></div>
  <h3>ABOUT RT <span>SNACKWORKS,LLC</span></h3>
  <div class="rule" style="left:615px;top:130px"></div>
  <p style="top:171px">At RT Snackworks, we are dedicated to revolutionizing the vending experience. Our mission is to provide a convenient way for favorite snacks and drinks in a hassle-free manner.</p>
  <p style="top:256px">With a focus on customer satisfaction, we ensure that our products are always fresh and our machines are ell-maintained. Experience the future of vending with RT Snackworks, LLC.</p>
  <a class="btn" style="left:643px;top:345px;width:123px;height:46px">READ MORE</a>
</section>

<section class="why">
  <h3 class="section-title" style="top:49px">WHY <span>CHOOSE US</span></h3>
  <div class="rule" style="left:567px;top:100px"></div>
  <p class="lead">RT Snackworks stands out for its commitment to quality, convenience, and customization. We prioritize customer preferences and aim to provide a seamless vending experience.</p>

  <div class="card" style="left:115px;top:234px;width:290px;height:335px">
    <div class="icon"><svg width="44" height="44" viewBox="0 0 44 44" fill="none" stroke="#fff" stroke-width="2"><circle cx="22" cy="15" r="9"/><path d="M18 15l3 3 5-6"/><path d="M4 32l8-4h10l6 3h10v4H18"/></svg></div>
    <h4>QUALITY PRODUCTS</h4>
    <p>Our vending machines are stocked with a diverse range of snacks and drinks, ensuring that there's something for everyone. We source only the freshest products for your enjoyment.</p>
    <div class="more">LEARN MORE</div>
  </div>
  <div class="card" style="left:456px;top:234px;width:290px;height:335px">
    <div class="icon"><svg width="44" height="44" viewBox="0 0 44 44" fill="none" stroke="#fff" stroke-width="2"><circle cx="24" cy="16" r="11"/><path d="M24 10v6l4 3"/><path d="M4 34l8-4h10l6 3h10v4H18"/></svg></div>
    <h4>CONVENIENCE</h4>
    <p>With RT Snackworks, snack time is just a swipe away. Our machines are strategically located for your convenience, providing quick and easy access to your favorite treats.</p>
    <div class="more">LEARN MORE</div>
  </div>
  <div class="card" style="left:799px;top:234px;width:290px;height:335px">
    <div class="icon"><svg width="44" height="44" viewBox="0 0 44 44" fill="none" stroke="#fff" stroke-width="2"><circle cx="22" cy="22" r="14"/><circle cx="22" cy="22" r="7"/><path d="M14 30l14-14"/></svg></div>
    <h4>CUSTOMIZATION</h4>
    <p>Personalize your snacking experience with RT Snackworks. Choose from a wide selection of snacks and drinks to create a vending experience that suits your unique preferences.</p>
    <div class="more">LEARN MORE</div>
  </div>
</section>

<section class="portfolio">
  <h3 class="section-title" style="top:80px">OUR <span>PORTFOLIO</span></h3>
  <div class="rule" style="left:567px;top:130px"></div>
  <div class="tile" style="left:111px;top:178px;width:399px;height:238px;background:linear-gradient(135deg,#1e2a33,#3a3f45 50%,#7a6f62)" role="img" aria-label="Snack wall and drink cooler in an office break room"></div>
  <div class="tile" style="left:519px;top:178px;width:280px;height:238px;background:linear-gradient(135deg,#cfd4d8,#3b3f44 50%,#8a8f94)" role="img" aria-label="Single vending machine by a glass storefront"></div>
  <div class="tile" style="left:808px;top:178px;width:281px;height:238px;background:linear-gradient(135deg,#3a4550,#5d6b73 50%,#a6b3b8)" role="img" aria-label="Two vending machines beside a plant by a window"></div>
  <div class="tile" style="left:111px;top:427px;width:281px;height:238px;background:linear-gradient(135deg,#5a3a2a,#1b2b3a 45%,#3b6ea0 70%,#2a2a2a)" role="img" aria-label="Two-door micro market cooler against brick"></div>
  <div class="tile" style="left:401px;top:427px;width:280px;height:238px;background:linear-gradient(135deg,#2a2a2a,#111)" role="img" aria-label="Dark vending machine close-up"></div>
  <a class="btn" style="left:480px;top:557px;width:123px;height:46px">VIEW MORE</a>
  <div class="tile" style="left:690px;top:427px;width:399px;height:238px;background:linear-gradient(135deg,#d9d9d9,#2b3a44 40%,#3a7a6a 60%,#c9c9c9)" role="img" aria-label="Row of coolers and snack racks in a micro market"></div>
</section>

<section class="blog">
  <h3 class="section-title" style="top:48px">OUR <span>LATEST BLOG</span></h3>
  <div class="rule" style="left:567px;top:99px"></div>
  <div class="post" style="left:115px">
    <div class="post-photo" role="img" aria-label="Customer choosing a drink from an open cooler"></div>
    <h4>LOREM IPSUM DOLOR SIT</h4>
    <p>Lorem ipsum dolor sit amet, consectur adipiscing elit, sed do eiusmod empor incididunt ut labore et dolore magna aliqua Quis ipsum.</p>
    <div class="more">READ MORE</div>
  </div>
  <div class="post" style="left:448px">
    <div class="post-photo" role="img" aria-label="Customer looking at a vending machine at night"></div>
    <h4>LOREM IPSUM DOLOR SIT</h4>
    <p>Lorem ipsum dolor sit amet, consectur adipiscing elit, sed do eiusmod empor incididunt ut labore et dolore magna aliqua Quis ipsum.</p>
    <div class="more">READ MORE</div>
  </div>
  <div class="post" style="left:780px">
    <div class="post-photo" style="background:linear-gradient(135deg,#1a1a1a,#4a4a4a 50%,#222)" role="img" aria-label="Row of dark snack vending machines"></div>
    <h4>LOREM IPSUM DOLOR SIT</h4>
    <p>Lorem ipsum dolor sit amet, consectur adipiscing elit, sed do eiusmod empor incididunt ut labore et dolore magna aliqua Quis ipsum.</p>
    <div class="more">READ MORE</div>
  </div>
</section>
<svg class="arrow" style="left:38px" viewBox="0 0 34 34"><circle cx="17" cy="17" r="17" fill="#111"/><path d="M19 11l-6 6 6 6" stroke="#fff" stroke-width="2.5" fill="none"/></svg>
<svg class="arrow" style="left:1128px" viewBox="0 0 34 34"><circle cx="17" cy="17" r="16" fill="#fff" stroke="#111" stroke-width="1.5"/><path d="M15 11l6 6-6 6" stroke="#111" stroke-width="2" fill="none"/></svg>

<footer class="site-footer">
  <div class="abs" style="left:0;width:1200px;top:112px;display:flex;justify-content:center">
    <div class="brand"><span class="brand-mark"></span>RT Snackworks, LLC</div>
  </div>
  <nav class="links">
    <a style="left:410px">HOME</a>
    <a style="left:523px">ABOUT US</a>
    <a style="left:667px">WHY CHOOSE US</a>
  </nav>
  <hr>
  <div class="copy">Copyright© 2024 <a>RT Snackworks,LLC</a> &nbsp;|&nbsp; All Rights Reserved</div>
</footer>

</body>
</html>
```